Velmora Isle is a premium Spa and Salon only professional tanning brand.

We need a email template/newsletter that we can send to our client base any time we would like to share information with them.
Whether this is launching our Christmas gift, or sharing up and coming training dates it will be another avenue for us to stay in touch with our clients.
We like to think ourselves as the 'Halvorne handbag' in the tanning world, Velmora Isle is a brand that is desirable and exclusive and has people hooked once they trial the brand and are blown away by the results.
www.velmora-isle.example

```html
<!DOCTYPE html>
<html lang="en">
<head>
<meta charset="utf-8">
<title>Velmora Isle – Newsletter</title>
<link rel="stylesheet" href="https://fonts.googleapis.com/css2?family=Cormorant+Garamond:wght@500&family=Mulish:wght@300;400&family=Tinos&display=swap">
<style>
  :root {
    --bg-top: #f8e0d0;
    --bg-bottom: #e7c2a7;
    --maroon: #8d4545;
    --tan: #dcae8c;
    --brown-text: #6b2b22;
    --brand: #8a3c33;
    --panel: #fdfaf8;
    --swatch-light: #dfbb92;
    --swatch-mid: #ad6a37;
    --swatch-dark: #76240f;
    --button-top: #a5564a;
    --button-bottom: #7a3530;
    --badge: #b86a3c;
    --icon-top: #c0886c;
    --icon-bottom: #7d3a30;
  }
  html, body {
    margin: 0;
    padding: 0;
    width: 746px;
    height: 1200px;
    overflow: hidden;
  }
  body {
    background: linear-gradient(180deg, var(--bg-top) 0%, #f3d3bf 55%, var(--bg-bottom) 100%);
    font-family: "Mulish", "Helvetica Neue", Arial, sans-serif;
    color: var(--brown-text);
    position: relative;
  }
  .newsletter { position: relative; width: 746px; height: 1200px; }

  .greeting {
    position: absolute; left: 36px; top: 22px;
    font-size: 16px; font-weight: 300; color: var(--brand);
  }
  .brand-name {
    position: absolute; right: 26px; top: 26px;
    font-family: "Cormorant Garamond", Georgia, serif;
    font-weight: 500; font-size: 50px; line-height: 0.95;
    color: var(--brand); text-align: right; letter-spacing: 1px;
    margin: 0;
  }
  .site-url {
    position: absolute; left: 345px; top: 110px;
    font-size: 17px; font-weight: 300; color: var(--brand);
  }

  .frame {
    position: absolute; left: 23px; top: 149px; width: 697px; height: 841px;
    background: linear-gradient(100deg, var(--maroon) 0%, #b06c56 35%, var(--tan) 55%, #b06c56 75%, var(--maroon) 100%);
  }
  .frame::after {
    content: ""; position: absolute; left: 0; right: 0; top: 120px; bottom: 0;
    background: var(--maroon);
  }
  .panel {
    position: absolute; left: 18px; top: 26px; width: 663px; height: 791px;
    background: var(--panel); overflow: hidden; z-index: 1;
  }
  .model-backdrop {
    position: absolute; left: 0; top: 300px; width: 390px; height: 491px;
    background: radial-gradient(ellipse at 40% 55%, rgba(214,170,140,0.45) 0%, rgba(240,215,195,0.3) 45%, rgba(253,250,248,0) 75%);
  }
  .headline {
    position: absolute; left: 0; right: 0; top: 26px; margin: 0;
    font-family: "Cormorant Garamond", Georgia, serif; font-weight: 500;
    font-size: 27px; line-height: 32px; text-align: center; color: var(--brown-text);
  }
  .product-shot {
    position: absolute; left: 26px; top: 120px; width: 163px; height: 140px;
    background: linear-gradient(160deg, #efe7e1 0%, #e4d6cb 60%, #d8bfa8 100%);
  }
  .intro {
    position: absolute; left: 200px; top: 120px; width: 420px; margin: 0;
    font-size: 17px; line-height: 23px; font-weight: 300; text-align: justify;
  }
  .swatches { position: absolute; left: 23px; top: 281px; width: 166px; }
  .swatch { height: 14px; margin-bottom: 14px; }
  .swatch--light { background: var(--swatch-light); }
  .swatch--medium { background: var(--swatch-mid); }
  .swatch--dark { background: var(--swatch-dark); }

  .timing-title {
    position: absolute; left: 200px; top: 266px; margin: 0;
    font-size: 17px; font-weight: 300;
  }
  .timing-list {
    position: absolute; left: 200px; top: 296px; margin: 0; padding-left: 56px;
    font-size: 17px; line-height: 24px; font-weight: 300;
  }
  .timing-list li { padding-left: 12px; }
  .choose {
    position: absolute; left: 200px; top: 402px; margin: 0;
    font-size: 17px; font-weight: 300;
  }
  .read-more {
    position: absolute; width: 96px; height: 27px;
    background: linear-gradient(180deg, var(--button-top), var(--button-bottom));
    border-radius: 3px; color: #fff; font-size: 13px; font-weight: 400;
    line-height: 27px; text-align: center; text-decoration: none; letter-spacing: 0.3px;
  }
  .read-more--intro { left: 200px; top: 439px; }
  .read-more--formula { left: 23px; top: 677px; width: 98px; }

  .formula-title {
    position: absolute; left: 63px; top: 500px; margin: 0;
    font-size: 19px; font-weight: 300;
  }
  .formula-text {
    position: absolute; left: 27px; top: 545px; width: 331px; margin: 0;
    font-size: 17px; line-height: 23.5px; font-weight: 300; text-align: justify;
  }

  .range-visual { position: absolute; left: 395px; top: 522px; }

  .footer-icons { position: absolute; left: 29px; top: 1003px; }
  .address {
    position: absolute; left: 270px; top: 1017px; width: 210px;
    font-family: "Tinos", "Times New Roman", serif; font-size: 10px; line-height: 12px;
    text-align: center; color: #3e2a26;
  }
  .address strong { font-weight: 700; }
  .badges { position: absolute; left: 520px; top: 1003px; }

  .footer-links {
    position: absolute; left: 0; right: 0; top: 1130px; text-align: center;
    font-size: 17px; font-weight: 300; color: var(--brand);
  }
</style>
</head>
<body>
<main class="newsletter">
  <header>
    <p class="greeting" style="margin:0">Hello Clara, see what’s new at Velmora Isle!</p>
    <h1 class="brand-name">Velmora<br>Isle</h1>
    <span class="site-url">www.velmora-isle.example</span>
  </header>

  <section class="frame">
    <div class="panel">
      <div class="model-backdrop" role="img" aria-label="Soft faded photo of a woman wrapped in a towel, surrounded by autumn leaves"></div>

      <h2 class="headline">Great news!<br>The 2-6 hour tanning revolution has arrived!</h2>

      <div class="product-shot" role="img" aria-label="Campaign image of tanned legs among falling autumn leaves"></div>
      <p class="intro">This revolutionary new rapid tanning product takes just 2-6 hours to develop, and allows you to control the depth of your tan by choosing for yourself when to shower it off.</p>

      <div class="swatches" aria-hidden="true">
        <div class="swatch swatch--light"></div>
        <div class="swatch swatch--medium"></div>
        <div class="swatch swatch--dark"></div>
      </div>

      <p class="timing-title">Showering times to achieve your desired colour:</p>
      <ul class="timing-list">
        <li>Light - Shower at 2 hours</li>
        <li>Medium - Shower at 4 hours</li>
        <li>Dark - Shower at 6 hours</li>
      </ul>
      <p class="choose">Now you can choose your colour!</p>
      <a class="read-more read-more--intro" href="#">READ MORE</a>

      <h3 class="formula-title">A revolution in self tanning</h3>
      <p class="formula-text">Velmora Isle has been developed with a unique organic formula, enriched with deep moisturisers and free from paraben and alcohol, ensuring a streak-free, soft finish.</p>
      <a class="read-more read-more--formula" href="#">READ MORE</a>

      <svg class="range-visual" width="260" height="260" viewBox="0 0 260 260">
        <defs>
          <linearGradient id="ringGrad" x1="0" y1="0" x2="1" y2="1">
            <stop offset="0" stop-color="#c48a66"/>
            <stop offset="1" stop-color="#8a3c33"/>
          </linearGradient>
          <linearGradient id="bottleGrad" x1="0" y1="0" x2="0" y2="1">
            <stop offset="0" stop-color="#f4f1ee"/>
            <stop offset="0.7" stop-color="#e8dfd8"/>
            <stop offset="1" stop-color="#c99a76"/>
          </linearGradient>
        </defs>
        <circle cx="128" cy="140" r="114" fill="none" stroke="url(#ringGrad)" stroke-width="8"/>
        <rect x="55" y="56" width="150" height="160" rx="10" fill="url(#bottleGrad)" role="img" aria-label="Product photo of three white tanning bottles"/>
        <circle cx="222" cy="60" r="38" fill="var(--badge)"/>
      </svg>
    </div>
  </section>

  <svg class="footer-icons" width="240" height="72" viewBox="0 0 240 72">
    <defs>
      <linearGradient id="iconGrad" x1="0" y1="0" x2="0" y2="1">
        <stop offset="0" stop-color="var(--icon-top)"/>
        <stop offset="1" stop-color="var(--icon-bottom)"/>
      </linearGradient>
    </defs>
    <circle cx="36" cy="36" r="35" fill="url(#iconGrad)"/>
    <rect x="18" y="24" width="36" height="25" fill="none" stroke="#fff" stroke-width="2"/>
    <polyline points="18,24 36,39 54,24" fill="none" stroke="#fff" stroke-width="2"/>
    <circle cx="120" cy="36" r="35" fill="url(#iconGrad)"/>
    <text x="120" y="40" text-anchor="middle" font-family="Mulish, sans-serif" font-size="10" fill="#fff">Friendloop</text>
    <circle cx="204" cy="36" r="35" fill="url(#iconGrad)"/>
    <text x="204" y="40" text-anchor="middle" font-family="Mulish, sans-serif" font-size="10" fill="#fff">Chirpline</text>
  </svg>

  <address class="address" style="font-style:normal">
    <strong>Velmora Isle</strong><br>
    Halden Park Enterprises<br>
    Orrin Lane Business Estate<br>
    Marlow Bay, County Keswin KB14 2QR
  </address>

  <svg class="badges" width="180" height="72" viewBox="0 0 180 72">
    <rect x="12" y="12" width="50" height="48" rx="8" fill="var(--badge)"/>
    <circle cx="141" cy="36" r="34" fill="var(--badge)"/>
  </svg>

  <footer class="footer-links">unsubscribe from this list &nbsp;| view email in browser</footer>
</main>
</body>
</html>
```